Small environmental consultancy needs a simple but professional web design

We are a boutique environmental consultancyand contracting business located in Margaret River in the South West of Western Australia.

We have two arms
1) Consulting which offers environmental planning, management and assessment services primarily to local government and the development industry.
2) Contracting which implements on site plans and on ground works primarily involving revegetation, bush regeneration and environmental weed control.

We need a simple yet professional web design within the wordpress platform that commmunicates professionalism, experience and technical expertise without appearing too corporate.

Something like this structure appeals:
http://fernquill.net.au/environment-services/
or
http://www.tallowbrookenvironmental.com.au/index.php

(without the image gallery function)

Target Market(s)

Local Government Officers deciding on tenders;
Developers, Engineers, Town Planning consultants looking for environmental expertise

Industry/Entity Type

Business

Number of Pages Required

5+ page

Font styles to use
Sans Serif

Colors
33a6d7
9bcb3c

Requirements
Must have
• Pages required include:
• Home
• Environmental Planning and Management
• Revegetation and Regeneration Implementation (This page can mirror the Environmental Planning and Management page exactly in structure but with different text and images)
• About Us (I think that this page can be relatively simple and generic)
• Contact (I think that this page can be very simple and generic)
Nice to have
• An ability to start out basic and quicikly establish a website presence and then build in additional drop downs and pages over time.
Should not have
• It does not need a photo gallery page;
• It does not need a major amount of space dedicated to social media and blogs etc as this is not currently particularly active area for us

```html
<!DOCTYPE html>
<html lang="en">
<head>
<meta charset="utf-8">
<title>Contact – Tarrawin Ecoservices</title>
<link rel="stylesheet" href="https://fonts.googleapis.com/css2?family=Open+Sans:ital,wght@0,400;0,600;0,700;1,400&family=Raleway:wght@700&family=Bebas+Neue&display=swap">
<style>
  :root {
    --blue: #33a6d7;
    --blue-dark: #2389c2;
    --green: #9bcb3c;
    --green-dark: #6f9a1c;
    --brown: #6e4420;
    --text: #333333;
    --muted: #555555;
    --placeholder: #9a9a9a;
    --panel: #efefef;
    --footer: #ebebeb;
    --line: #d4d4d4;
    --white: #ffffff;
    --required: #d42020;
    --icon-bg: #e3e3e3;
    --icon: #777777;
  }
  * { box-sizing: border-box; margin: 0; padding: 0; }
  html, body { width: 1087px; height: 1200px; overflow: hidden; background: var(--white); }
  body { font-family: "Open Sans", Arial, sans-serif; color: var(--text); }
  .page { position: relative; width: 1000px; height: 1104px; transform: scale(1.087); transform-origin: 0 0; }
  .abs { position: absolute; }

  /* Header */
  .header-scene { left: 0; top: 0; width: 1000px; height: 146px;
    background: linear-gradient(180deg, #f4f6f8 0%, #e3ebf1 45%, #c9d7e2 75%, #b5c8d6 100%); }
  .brand { left: 62px; top: 62px; display: flex; align-items: center; gap: 10px; }
  .brand-mark { width: 40px; height: 40px; border-radius: 50%; background: var(--green); }
  .brand-name { font-family: "Open Sans", sans-serif; font-weight: 600; font-size: 25px; color: var(--brown); }
  .call-label { left: 798px; top: 31px; font-size: 14px; font-weight: 600; color: #111; }
  .call-number { left: 798px; top: 45px; font-size: 24px; font-weight: 700; color: var(--blue); }
  .search { left: 761px; top: 87px; width: 177px; height: 23px; background: var(--white);
    border-radius: 3px; font-size: 12px; color: #666; padding: 4px 9px; }
  .search svg { position: absolute; right: 6px; top: 5px; }

  /* Navigation */
  .main-nav { left: 0; top: 146px; width: 1000px; height: 37px; background: var(--blue);
    border-bottom: 2px solid var(--blue-dark); }
  .main-nav a { position: absolute; top: 0; height: 35px; line-height: 35px; color: var(--white);
    font-family: "Raleway", sans-serif; font-weight: 700; font-size: 11.5px; text-decoration: none; }
  .main-nav a.active { background: var(--blue-dark); padding: 0 21px; }
  .banner { left: 0; top: 183px; width: 1000px; height: 105px;
    background: linear-gradient(90deg, #4b3b2a 0%, #8a6b45 20%, #6d6a55 40%, #b9c2b8 62%, #5c5a48 80%, #3f3a2e 100%); }

  /* Content */
  .page-title { left: 61px; top: 320px; font-family: "Bebas Neue", sans-serif; font-size: 35px; color: var(--green); }
  .form-panel { left: 62px; top: 381px; width: 576px; height: 403px; background: var(--panel); }
  .field-label { font-size: 11.5px; color: var(--text); }
  .field-label span { color: var(--required); }
  .input { background: var(--white); border: 1px solid #cfcfcf; border-radius: 3px; }
  .req-note { left: 540px; top: 718px; font-size: 11px; font-style: italic; color: #666; }
  .req-note span { color: var(--required); font-style: normal; }
  .submit { left: 84px; top: 727px; width: 178px; height: 33px; background: var(--green); border-radius: 2px;
    color: var(--white); font-family: "Bebas Neue", sans-serif; font-size: 20px; text-align: center; line-height: 35px; }

  .info-title { left: 661px; top: 378px; font-family: "Bebas Neue", sans-serif; font-size: 19px; color: #222; }
  .info-icon { width: 28px; height: 28px; border-radius: 50%; background: var(--icon-bg);
    display: flex; align-items: center; justify-content: center; }
  .info-text { font-size: 11px; line-height: 16px; color: var(--muted); }

  /* Footer */
  .site-footer { left: 0; top: 830px; width: 1000px; height: 274px; background: var(--footer); border-top: 1px solid var(--line); }
  .foot-title { font-family: "Bebas Neue", sans-serif; font-size: 19px; color: #333; }
  .foot-links { font-size: 11px; line-height: 17px; color: #444; }
  .foot-phone { left: 60px; top: 984px; display: flex; align-items: center; gap: 6px;
    font-family: "Bebas Neue", sans-serif; font-size: 29px; color: var(--green); }
  .foot-input { background: var(--white); border: 1px solid #d9d9d9; font-size: 12.5px; color: var(--placeholder); padding: 7px 10px; }
  .foot-input svg { position: absolute; right: 8px; }
  .send { left: 512px; top: 1002px; width: 130px; height: 35px; background: linear-gradient(180deg, #8fb82c, var(--green-dark));
    color: var(--white); font-family: "Bebas Neue", sans-serif; font-size: 18px; text-align: center; line-height: 37px; }
  .foot-rule { left: 62px; top: 1063px; width: 896px; height: 1px; background: var(--line); }
  .copyright { left: 62px; top: 1076px; font-size: 11px; color: #444; }
</style>
</head>
<body>
<div class="page">

  <header>
    <div class="abs header-scene" role="img" aria-label="Misty blue mountain ranges under a pale sky"></div>
    <div class="abs brand"><span class="brand-mark"></span><span class="brand-name">Tarrawin Ecoservices</span></div>
    <div class="abs call-label">Call Us</div>
    <div class="abs call-number">0412 738 604</div>
    <div class="abs search">Search
      <svg width="13" height="13" viewBox="0 0 13 13"><circle cx="5.5" cy="5.5" r="4.3" fill="none" stroke="#888" stroke-width="1.6"/><line x1="8.6" y1="8.6" x2="12" y2="12" stroke="#888" stroke-width="1.8"/></svg>
    </div>
  </header>

  <nav class="abs main-nav">
    <a style="left:84px">HOME</a>
    <a style="left:152px">ENVIRONMENTAL PLANNING AND MANAGEMENT</a>
    <a style="left:445px">REVEGETATION AND REGENERATION IMPLEMENTATION</a>
    <a style="left:772px">ABOUT US</a>
    <a class="active" style="left:841px">CONTACT</a>
  </nav>
  <div class="abs banner" role="img" aria-label="Sunlit forest with tall trunks and autumn foliage"></div>

  <main>
    <h1 class="abs page-title">Contact</h1>

    <div class="abs form-panel"></div>
    <div class="abs field-label" style="left:84px;top:405px">First Name<span>*</span></div>
    <div class="abs field-label" style="left:360px;top:405px">Last Name<span>*</span></div>
    <div class="abs input" style="left:84px;top:426px;width:254px;height:25px"></div>
    <div class="abs input" style="left:360px;top:426px;width:254px;height:25px"></div>
    <div class="abs field-label" style="left:84px;top:464px">Email<span>*</span></div>
    <div class="abs field-label" style="left:360px;top:464px">Phone Number<span>*</span></div>
    <div class="abs input" style="left:84px;top:485px;width:254px;height:25px"></div>
    <div class="abs input" style="left:360px;top:485px;width:254px;height:25px"></div>
    <div class="abs field-label" style="left:84px;top:527px">Message<span>*</span></div>
    <div class="abs input" style="left:84px;top:547px;width:531px;height:164px"></div>
    <div class="abs req-note"><span>*</span> Require field</div>
    <div class="abs submit">Submit</div>

    <h2 class="abs info-title">Contact Info</h2>
    <div class="abs info-icon" style="left:662px;top:411px">
      <svg width="10" height="13" viewBox="0 0 10 13"><path d="M5 0a4.5 4.5 0 0 1 4.5 4.5C9.5 8 5 13 5 13S.5 8 .5 4.5A4.5 4.5 0 0 1 5 0z" fill="var(--icon)"/><circle cx="5" cy="4.5" r="1.6" fill="var(--icon-bg)"/></svg>
    </div>
    <div class="abs info-text" style="left:700px;top:409px">228, Lorem ipsum dolor<br>sit aremt sor- 859584</div>
    <div class="abs info-icon" style="left:662px;top:461px">
      <svg width="12" height="12" viewBox="0 0 12 12"><path d="M2.5 0.5l2 2.6-1.2 1.3c.7 1.6 2 2.9 3.6 3.6l1.3-1.2 2.6 2-1.4 2.3C4.6 10.8 1.2 7.4.3 2z" fill="var(--icon)"/></svg>
    </div>
    <div class="abs info-text" style="left:700px;top:460px">Phone :<br>0412 738 604</div>
    <div class="abs info-icon" style="left:662px;top:516px">
      <svg width="13" height="11" viewBox="0 0 13 11"><path d="M.5 4L6.5.5 12.5 4v6.5h-12z" fill="var(--icon)"/><path d="M.8 4.2l5.7 3.5 5.7-3.5" fill="none" stroke="var(--icon-bg)" stroke-width="1"/></svg>
    </div>
    <div class="abs info-text" style="left:700px;top:514px">Email :<br>info@tarrawinecoservices.com.au</div>
  </main>

  <footer>
    <div class="abs site-footer"></div>
    <h3 class="abs foot-title" style="left:61px;top:856px">About</h3>
    <div class="abs foot-links" style="left:62px;top:884px">Environmental Planning and Management<br>Revegetation and Bush Regeneration<br>Contacts</div>
    <h3 class="abs foot-title" style="left:60px;top:961px">Call us now:</h3>
    <div class="abs foot-phone">
      <svg width="18" height="18" viewBox="0 0 12 12"><path d="M2.5 0.5l2 2.6-1.2 1.3c.7 1.6 2 2.9 3.6 3.6l1.3-1.2 2.6 2-1.4 2.3C4.6 10.8 1.2 7.4.3 2z" fill="#555"/></svg>
      0412 738 604
    </div>

    <h3 class="abs foot-title" style="left:313px;top:856px">Legal</h3>
    <div class="abs foot-links" style="left:314px;top:884px">Terms of Service<br>Privacy Policy<br>Cookie Policy</div>
    <h3 class="abs foot-title" style="left:313px;top:961px">Website</h3>
    <div class="abs foot-links" style="left:314px;top:989px">www.tarrawinecoservices.com.au</div>

    <h3 class="abs foot-title" style="left:512px;top:856px">Contact Us</h3>
    <div class="abs foot-input" style="left:512px;top:894px;width:208px;height:30px">Name
      <svg style="top:7px" width="16" height="16" viewBox="0 0 16 16"><circle cx="8" cy="4.5" r="4" fill="#bbb"/><path d="M0 16c0-5 3.5-7 8-7s8 2 8 7z" fill="#bbb"/></svg>
    </div>
    <div class="abs foot-input" style="left:729px;top:894px;width:208px;height:30px">E-mail
      <svg style="top:9px" width="18" height="13" viewBox="0 0 18 13"><rect width="18" height="13" fill="#bbb"/><path d="M0 0l9 7 9-7" fill="none" stroke="#fff" stroke-width="1.3"/></svg>
    </div>
    <div class="abs foot-input" style="left:512px;top:933px;width:425px;height:60px">Message
      <svg style="top:5px" width="18" height="15" viewBox="0 0 18 15"><path d="M0 0h18v11H6l-4 4v-4H0z" fill="#bbb"/><circle cx="5" cy="5.5" r="1.2" fill="#fff"/><circle cx="9" cy="5.5" r="1.2" fill="#fff"/><circle cx="13" cy="5.5" r="1.2" fill="#fff"/></svg>
    </div>
    <div class="abs send">Send Message</div>

    <div class="abs foot-rule"></div>
    <div class="abs copyright">© 2015 Tarrawin Ecoservices. All Rights Reserved.</div>
  </footer>

</div>
</body>
</html>
```